New Business Card for our Indoor Golf Training Facility

We are looking for designs for a new business card for our indoor golf training facility. Attached is our logo, our logo with our slogan, and here is our elevator pitch (What makes us different from the others) not sure if all the info will fit on one card, maybe you can condense the elevator pitch? here is the info

Elevator Pitch
We work with serious golfers and those that want to be serious golfers…
to make you better, faster, at all phases of the game…
We use the same state-of-the-art technology as professional golfers…
which produces data sets that shows your improvement in real time.
Our facility is available 24/7 to our members, which allows you to improve on your time.

our website: www.birchpinlinks.com

Target Market(s)

Golfers

Font styles to use
Serif
Sans Serif

Colors
ec1f27
f59195
fbd4d5
919191
d3d3d3
1b1b1b

Requirements
Must have
• our logo or our logo with the slogan, elevator pitch (can be condensed or shortened)

```html
<!DOCTYPE html>
<html lang="en">
<head>
<meta charset="utf-8">
<title>Birch Pin Links – Business Card</title>
<link rel="stylesheet" href="https://fonts.googleapis.com/css2?family=Roboto:wght@400;500;700;900&family=Roboto+Condensed:wght@400;700&display=swap">
<style>
  :root {
    --red: #ec1f27;
    --red-soft: #e33a37;
    --pink: #f59195;
    --blush: #fbd4d5;
    --grey: #919191;
    --light-grey: #d3d3d3;
    --ink: #1b1b1b;
    --paper: #f7f7f7;
    --stage: #ececec;
  }
  * { box-sizing: border-box; margin: 0; padding: 0; }
  html, body { width: 1200px; height: 911px; overflow: hidden; }
  body {
    background: var(--stage);
    font-family: "Roboto", Arial, sans-serif;
    position: relative;
  }
  .card {
    position: absolute;
    width: 540px;
    height: 309px;
    background: var(--paper);
    border-radius: 22px;
    overflow: hidden;
    box-shadow: 0 6px 18px rgba(0,0,0,.18);
  }
  /* front */
  .card--front { left: 60px; top: 110px; }
  .front__band {
    position: absolute; left: 0; top: 0; width: 100%; height: 96px;
    background: var(--red-soft);
  }
  .front__person { position: absolute; left: 36px; top: 126px; }
  .person__name { color: var(--red); font-weight: 700; font-size: 27px; line-height: 1.1; }
  .person__role { color: var(--ink); font-weight: 500; font-size: 15px; margin-top: 2px; }
  .front__contact {
    position: absolute; left: 36px; top: 194px;
    color: #555; font-size: 14px; line-height: 1.45;
  }
  .contact__row { display: flex; align-items: center; gap: 7px; }
  .contact__row svg { width: 12px; height: 12px; fill: var(--red); flex: none; }
  .front__brand { position: absolute; right: 30px; bottom: 34px; text-align: right; }
  .brand__name { color: var(--red); font-weight: 900; font-size: 34px; line-height: 1; }
  .brand__slogan { color: var(--red); font-size: 13px; margin-top: 4px; }
  /* back */
  .card--back { left: 600px; top: 490px; }
  .back__brand {
    position: absolute; left: 0; top: 34px; width: 100%;
    display: flex; justify-content: center; align-items: center; gap: 14px;
  }
  .brand__dot {
    width: 42px; height: 42px; border-radius: 50%;
    border: 4px solid var(--red);
  }
  .back__brand .brand__name { font-size: 38px; }
  .back__brand .brand__slogan { text-align: left; }
  .pitch {
    position: absolute; left: 0; bottom: 0; width: 100%; height: 168px;
    background: var(--red);
    color: #fff;
    font-family: "Roboto Condensed", "Arial Narrow", sans-serif;
    text-align: center;
    padding: 30px 20px 0;
  }
  .pitch__tab {
    position: absolute; left: 50%; top: -14px; transform: translateX(-50%);
    background: var(--paper); color: var(--red);
    font-weight: 700; font-size: 15px; letter-spacing: .5px;
    padding: 4px 14px; border-radius: 14px 14px 0 0;
  }
  .pitch__text { font-size: 13.5px; line-height: 1.4; }
  .pitch__social {
    display: flex; justify-content: center; gap: 6px; margin-top: 8px;
  }
  .pitch__social span {
    width: 16px; height: 16px; border-radius: 50%; background: #fff;
  }
</style>
</head>
<body>
  <section class="card card--front" aria-label="Business card front">
    <div class="front__band"></div>
    <div class="front__person">
      <p class="person__name">Dana Whitfield</p>
      <p class="person__role">CEO/Founder</p>
    </div>
    <div class="front__contact">
      <p>1480 Fairway Crossing, Suite B4</p>
      <p>Millbrook, OH 45990</p>
      <p class="contact__row">
        <svg viewBox="0 0 24 24" aria-hidden="true"><path d="M6.6 10.8a15.1 15.1 0 006.6 6.6l2.2-2.2a1 1 0 011-.25 11.4 11.4 0 003.6.6 1 1 0 011 1V20a1 1 0 01-1 1A17 17 0 013 4a1 1 0 011-1h3.5a1 1 0 011 1 11.4 11.4 0 00.6 3.6 1 1 0 01-.25 1z"/></svg>
        555-204-7781
      </p>
      <p class="contact__row">
        <svg viewBox="0 0 24 24" aria-hidden="true"><path d="M2 5h20v14H2z M2 5l10 8 10-8" /></svg>
        info@birchpinlinks.com
      </p>
      <p class="contact__row">
        <svg viewBox="0 0 24 24" aria-hidden="true"><circle cx="12" cy="12" r="10"/></svg>
        birchpinlinks.com
      </p>
    </div>
    <div class="front__brand">
      <p class="brand__name">Birch Pin Links</p>
      <p class="brand__slogan">Play Well. Play Often. Play Better.</p>
    </div>
  </section>

  <section class="card card--back" aria-label="Business card back">
    <div class="back__brand">
      <span class="brand__dot"></span>
      <div>
        <p class="brand__name">Birch Pin Links</p>
        <p class="brand__slogan">Play Well. Play Often. Play Better.</p>
      </div>
    </div>
    <div class="pitch">
      <p class="pitch__tab">ELEVATOR PITCH:</p>
      <p class="pitch__text">
        We work with serious golfers and those that want to be serious golfers…<br>
        to make you better, faster, at all phases of the game…<br>
        We use the same state-of-the-art technology as professional golfers…<br>
        which produces data sets that shows your improvement in real time.<br>
        Our facility is available 24/7 to our members, which allows you to improve on your time.
      </p>
      <div class="pitch__social" aria-hidden="true"><span></span><span></span></div>
    </div>
  </section>
</body>
</html>
```